Woman owned consulting company needs an elegant and modern business card design

I need a business card design for my new consulting company, Mara Quillon Consulting. I am looking for something that is simple and elegant, but also creative and original. You can use either version of the logo that are attached. I have also included the information that needs to be featured on the business card.

Contact Information for Business Card

Requirements
Must have
• The logo and the font type and a standard business card size. Use shades of gray/silver and or rose gold that are in the logo.
• I didn't realize that my actual logo wasn't attached. Please incorporate in the designs.
Should not have
• Colors that are different from my logo

```html
<!DOCTYPE html>
<html lang="en">
<head>
<meta charset="utf-8">
<title>Mara Quillon Consulting – Business Cards</title>
<link href="https://fonts.googleapis.com/css2?family=Arimo:wght@400;700&display=swap" rel="stylesheet">
<style>
  :root {
    --backdrop: #7a7a7a;
    --card-light: #ececef;
    --card-smoke: #8a8a8b;
    --ink-grey: #5e5e61;
    --ink-soft: #6a6a6d;
    --mark-pale: #d3d3d7;
    --foil-silver: #dcdcde;
  }
  * { margin: 0; padding: 0; box-sizing: border-box; }
  html, body {
    width: 1200px;
    height: 1016px;
    overflow: hidden;
    background: var(--backdrop);
    font-family: "Arimo", Arial, sans-serif;
  }
  .card {
    position: absolute;
    left: 332px;
    width: 549px;
    height: 314px;
  }
  .card--front { top: 131px; background: var(--card-light); }
  .card--back  { top: 514px; background: var(--card-smoke); }

  .contact {
    position: absolute;
    left: 49px;
    top: 200px;
    color: var(--ink-soft);
    text-transform: uppercase;
  }
  .contact__title {
    font-size: 12.5px;
    letter-spacing: 0.2px;
    margin-bottom: 16px;
  }
  .contact__name { font-weight: 700; color: var(--ink-grey); }
  .contact__line {
    font-size: 10.2px;
    line-height: 18px;
  }

  .brand-mark {
    position: absolute;
    right: 50px;
    top: 208px;
    text-align: right;
    color: var(--mark-pale);
    font-size: 17px;
    line-height: 21px;
    font-weight: 400;
  }

  .brand-wordmark {
    position: absolute;
    left: 0;
    right: 0;
    top: 118px;
    text-align: center;
    color: var(--foil-silver);
    font-size: 34px;
    font-weight: 400;
    letter-spacing: 1px;
    line-height: 42px;
  }
</style>
</head>
<body>
  <section class="card card--front">
    <div class="contact">
      <p class="contact__title"><span class="contact__name">Mara Quillon</span>&nbsp; / &nbsp;Owner</p>
      <p class="contact__line">555-014-2736 &nbsp;/&nbsp; mara@maraquillonconsulting.com</p>
      <p class="contact__line">www.maraquillonconsulting.com</p>
    </div>
    <div class="brand-mark">Mara Quillon<br>Consulting</div>
  </section>

  <section class="card card--back">
    <p class="brand-wordmark">Mara Quillon Consulting</p>
  </section>
</body>
</html>
```